Luxury Real Estate Website, Midwest, United States

We need web design services for a luxury website. We need IDX Integration with our MLS. We want this to be a very simple website with amazing graphics. We want it to link up with our MailChimp account in order to generate leads through a "More Information" Pop up on the main page. We want the main page to be covered with one large graphic that is a rolling slideshow of active listings of $400,000 and up from the IDX Integration. We need this website to give a very exclusive and sleek look. Lots of black is good... I will upload our logos in Black and Silver. We will also need an "About" page that we are going to call "Qeno Info". We want our graphics to be extremely impressive. Keep in mind, we are a company in the Midwest of the United States, and our real estate has a different look than homes in California or Florida. We need graphics that are realistic for the Midwest, yet still high-end.
Target Market(s)
Luxury Homeowners in the Midwest United States. The graphics needs to be pristine.
Industry/Entity Type
Real Estate
Coding
Coded - Design and coding required
Number of Pages Required
3 page
Requirements
Must have
- Large graphics with IDX Integration. The photos of real estate need to represent real estate that is common in the Midwest, United States. We also need MailChimp integration. We need a pop up that is titled "My Free Market Analysis" that makes them fill out a contact form asking for Full Name, Email Address, Phone Number and Address. This needs to be a pop up on the front page and will integrate with our MailChimp account. We also need a page called "About Qe No Home". And another page where clients can download informational PDFs. The main component needs to be a front page search engine connected with the IDX to access active listings from our MLS. I attached our logos and a sample front page of a website. I would love for ours to look similar.
Nice to have
- Lake House photos on midwest lakes are a plus.
Should not have
- Should not have clutter. This website needs to be clean, luxurious and exclusive.

```html
<!DOCTYPE html>
<html lang="en">
<head>
<meta charset="utf-8">
<title>Hearthstone Realty Group</title>
<link href="https://fonts.googleapis.com/css2?family=Open+Sans:wght@400;600&family=Oswald:wght@400;500&family=Roboto+Condensed:wght@400;700&display=swap" rel="stylesheet">
<style>
:root{
  --black:#000;
  --ink:#0b0b0b;
  --footer:#111;
  --silver:#c9c9c9;
  --light:#f1f1f1;
  --card:#fff;
  --text:#8a8a8a;
  --gold:#c7b46a;
  --white:#fff;
  --field:#f7f7f7;
  --button:#2a2a2a;
  --modal:#e9e9e9;
}
*{margin:0;padding:0;box-sizing:border-box}
html,body{width:1200px;height:3209px;overflow:hidden;background:var(--black)}
body{position:relative;font-family:"Open Sans",sans-serif;color:var(--white)}
.abs{position:absolute}

/* header */
.site-header{position:absolute;left:0;top:0;width:1200px;height:100px;background:var(--black);z-index:3}
.brand{position:absolute;left:133px;top:30px;display:flex;align-items:center;gap:10px;font-family:"Open Sans",sans-serif;font-size:22px;font-weight:400;color:var(--silver);letter-spacing:1px}
.brand-mark{width:12px;height:12px;background:var(--silver)}
.main-nav{position:absolute;left:455px;top:40px;display:flex;gap:36px;font-size:13px;font-weight:600;letter-spacing:.5px}
.main-nav a{color:var(--white);text-decoration:none}

/* hero */
.hero{position:absolute;left:0;top:100px;width:1200px;height:585px;background:linear-gradient(180deg,#3d4a58 0%,#6a6457 28%,#4b5a33 52%,#2f4522 72%,#1a2614 100%)}
.hero-arrow{position:absolute;top:240px;width:30px;height:30px;border-radius:50%;background:rgba(0,0,0,.45);display:flex;align-items:center;justify-content:center}
.hero-search{position:absolute;left:349px;top:345px;width:501px;height:38px;display:flex}
.hero-search input{flex:1;border:0;background:rgba(255,255,255,.9);padding:0 14px;font:13px "Open Sans",sans-serif;color:#555}
.hero-search button{width:38px;border:0;background:#dcdcdc;display:flex;align-items:center;justify-content:center}
.hero-curve{position:absolute;left:0;top:445px}

/* features */
.features{position:absolute;left:0;top:685px;width:1200px;height:460px;background:var(--black)}
.feature{position:absolute;top:0;width:340px;text-align:center}
.feature.is-active{border:1px solid #2b2b2b;top:72px;height:388px}
.feature-icon{width:94px;height:94px;border-radius:50%;border:2px solid #cfcfcf;margin:0 auto;display:flex;align-items:center;justify-content:center}
.feature h3{font-family:"Open Sans",sans-serif;font-weight:400;font-size:19px;color:var(--gold);margin-top:22px}
.feature p{font-size:12px;line-height:20px;color:var(--text);width:260px;margin:10px auto 0}
.btn-outline{display:inline-block;border:1.5px solid #d8d8d8;border-radius:5px;color:#ddd;font-size:12px;padding:4px 16px;margin-top:22px}

/* welcome */
.welcome{position:absolute;left:0;top:1145px;width:1200px;height:406px;background:linear-gradient(135deg,#4a4237 0%,#5c5244 35%,#3c3a2e 65%,#2a2a22 100%);text-align:center}
.welcome h2{font-family:"Roboto Condensed",sans-serif;font-weight:700;font-size:40px;color:#e8e8e8;margin-top:106px}
.welcome p{font-size:12.5px;line-height:24px;color:#cfcfcf;width:800px;margin:14px auto 0}
.welcome .btn-outline{margin-top:18px;font-size:14px;padding:6px 16px;border-radius:3px}

/* listings */
.listings{position:absolute;left:0;top:1551px;width:1200px;height:873px;background:var(--light)}
.listings h2{font-family:"Roboto Condensed",sans-serif;font-weight:700;font-size:31px;color:#222;text-align:center;margin-top:74px}
.card{position:absolute;width:296px;height:285px;background:var(--card);border:1px solid #e2e2e2}
.card-photo{height:163px;position:relative}
.card-tag{position:absolute;right:0;top:22px;background:rgba(255,255,255,.85);color:#333;font-size:9px;font-weight:600;padding:5px 14px}
.card-text{font-size:10.5px;line-height:14px;color:#777;padding:16px 16px 0}
.card-foot{position:absolute;left:0;bottom:0;width:100%;height:42px;border-top:1px solid #eee;display:flex;align-items:center;justify-content:space-between;padding:0 16px;font-size:11px;color:#666}
.card-foot span{display:flex;align-items:center;gap:6px}
.card-price{border-left:1px solid #eee;padding-left:14px;height:42px;display:flex;align-items:center}

/* news */
.news{position:absolute;left:0;top:2424px;width:1200px;height:410px;background:var(--ink)}
.news h2{position:absolute;left:130px;top:82px;font-family:"Roboto Condensed",sans-serif;font-weight:700;font-size:24px;color:#ddd}
.news-item{position:absolute;top:151px;display:flex;gap:24px}
.news-photo{width:176px;height:150px}
.news-body{width:240px}
.news-body h4{font-weight:400;font-size:15px;color:#e6e6e6}
.news-date{font-size:11px;color:#bbb;margin-top:12px}
.news-body p{font-size:10.5px;line-height:16px;color:#999;margin-top:10px}
.news-more{font-size:11px;color:#bbb;margin-top:10px}

/* footer */
.site-footer{position:absolute;left:0;top:2834px;width:1200px;height:375px;background:var(--footer)}
.footer-brand{position:absolute;left:130px;top:97px;display:flex;align-items:center;gap:8px;font-size:19px;color:var(--silver)}
.footer-brand .brand-mark{width:10px;height:10px}
.social{position:absolute;left:130px;top:155px;display:flex;gap:8px}
.social span{width:24px;height:24px;border-radius:50%;background:#bdbdbd}
.footer-col{position:absolute;top:48px}
.footer-col h5{font-family:"Roboto Condensed",sans-serif;font-weight:700;font-size:17px;color:#cfcfcf;margin-bottom:26px}
.contact-line{display:flex;gap:14px;font-size:11px;line-height:15px;color:#999;margin-bottom:14px}
.contact-line svg{flex:none;margin-top:1px}
.signup p{font-size:10.5px;line-height:15px;color:#999;width:220px}
.signup input{display:block;margin-top:14px;width:220px;height:36px;background:#ddd;border:0;padding:0 10px;font:11px "Open Sans",sans-serif;color:#777}
.signup button{display:block;margin-top:13px;width:92px;height:34px;background:#e6e6e6;border:0;font:600 10px "Open Sans",sans-serif;color:#333}
.quick-links a{display:block;font-size:11px;color:#999;text-decoration:none;line-height:24px}
.copyright{position:absolute;left:0;top:322px;width:1200px;text-align:center;font-size:11px;color:#8a8a8a}

/* modal */
.overlay{position:absolute;left:0;top:0;width:1200px;height:3209px;background:rgba(0,0,0,.68);z-index:10}
.modal{position:absolute;left:430px;top:171px;width:338px;height:417px;background:var(--modal);z-index:11;text-align:center}
.modal-close{position:absolute;right:14px;top:21px;width:22px;height:22px;border:1.5px solid #333;border-radius:50%;display:flex;align-items:center;justify-content:center}
.modal-mark{width:54px;height:54px;border-radius:50%;background:#bfbfbf;margin:34px auto 0}
.modal h3{font-family:"Oswald",sans-serif;font-weight:400;font-size:25px;color:#111;margin-top:14px}
.modal-form{width:246px;margin:12px auto 0}
.modal-form input{display:block;width:100%;height:34px;margin-bottom:13px;border:1px solid #ddd;background:var(--field);padding:0 12px;font:11px "Open Sans",sans-serif;color:#444}
.modal-form button{display:block;width:100%;height:36px;border:0;background:var(--button);color:var(--white);font:500 15px "Oswald",sans-serif;margin-top:4px}
</style>
</head>
<body>

<header class="site-header">
  <div class="brand"><span class="brand-mark"></span>HEARTHSTONE REALTY</div>
  <nav class="main-nav">
    <a href="#">HOME</a>
    <a href="#">ABOUT QE NO HOME</a>
    <a href="#">RESOURCES</a>
    <a href="#">MY MARKET ANALYSIS</a>
    <a href="#">CONTACT US</a>
  </nav>
</header>

<section class="hero" role="img" aria-label="Slideshow photo of a lakeside Midwest home at dusk">
  <div class="hero-arrow" style="left:100px"><svg width="12" height="12" viewBox="0 0 12 12"><path d="M8 1L3 6l5 5" fill="none" stroke="#fff" stroke-width="2"/></svg></div>
  <div class="hero-arrow" style="left:1070px"><svg width="12" height="12" viewBox="0 0 12 12"><path d="M4 1l5 5-5 5" fill="none" stroke="#fff" stroke-width="2"/></svg></div>
  <form class="hero-search">
    <input type="text" value="Search home">
    <button type="button"><svg width="14" height="14" viewBox="0 0 14 14"><circle cx="6" cy="6" r="4.5" fill="none" stroke="#333" stroke-width="1.6"/><path d="M9.5 9.5L13 13" stroke="#333" stroke-width="1.6"/></svg></button>
  </form>
  <svg class="hero-curve" width="1200" height="140" viewBox="0 0 1200 140">
    <path d="M0 0 Q600 170 1200 0 L1200 140 L0 140Z" fill="#000"/>
    <path d="M40 30 Q600 175 1160 30" fill="none" stroke="#cfcfcf" stroke-width="5"/>
    <path d="M120 50 Q600 168 1080 50" fill="none" stroke="#6a6a6a" stroke-width="3"/>
  </svg>
</section>

<section class="features">
  <div class="feature" style="left:91px;top:118px">
    <div class="feature-icon"><svg width="44" height="40" viewBox="0 0 44 40"><path d="M4 20L22 4l18 16M9 16v20h26V16" fill="none" stroke="#ddd" stroke-width="3"/><rect x="18" y="24" width="8" height="12" fill="#ddd"/></svg></div>
    <h3>Quis autem vel eum</h3>
    <p>Nemo enim ipsam voluptatem quia voluptas sit aspernatur aut odit aut fugit, sed quia consequuntur magni dolores</p>
    <span class="btn-outline">Read More</span>
  </div>
  <div class="feature is-active" style="left:430px">
    <div style="height:46px"></div>
    <div class="feature-icon"><svg width="40" height="40" viewBox="0 0 40 40"><path d="M4 4h16l16 16-16 16L4 20z" fill="#ddd"/><circle cx="12" cy="12" r="3" fill="#000"/></svg></div>
    <h3>Quis autem vel eum</h3>
    <p>Nemo enim ipsam voluptatem quia voluptas sit aspernatur aut odit aut fugit, sed quia consequuntur magni dolores</p>
    <span class="btn-outline">Read More</span>
  </div>
  <div class="feature" style="left:769px;top:118px">
    <div class="feature-icon"><svg width="44" height="40" viewBox="0 0 44 40"><rect x="4" y="4" width="36" height="24" rx="2" fill="none" stroke="#ddd" stroke-width="3"/><path d="M22 28v6M14 36h16" stroke="#ddd" stroke-width="3"/></svg></div>
    <h3>Quis autem vel eum</h3>
    <p>Nemo enim ipsam voluptatem quia voluptas sit aspernatur aut odit aut fugit, sed quia consequuntur magni dolores</p>
    <span class="btn-outline">Read More</span>
  </div>
</section>

<section class="welcome" role="img" aria-label="Background photo of a wooden deck overlooking a wooded lake">
  <h2>WELCOME TO HEARTHSTONE REALTY GROUP</h2>
  <p>Nemo enim ipsam voluptatem quia voluptas sit aspernatur aut odit aut fugit, sed quia consequuntur magni dolores eos qui ratione voluptatem sequi nesciunt. Neque porro quisquam est, qui dolorem ipsum quia dolor sit amet, consectetur. Nemo enim ipsam voluptatem quia voluptas sit aspernatur aut odit aut fugit, sed quia consequuntur magni dolores eos qui ratione</p>
  <span class="btn-outline">READ MORE</span>
</section>

<section class="listings">
  <h2>PROPERTIES LISTINGS</h2>

  <article class="card" style="left:130px;top:177px">
    <div class="card-photo" role="img" aria-label="Photo of a modern two-storey home with lit windows" style="background:linear-gradient(180deg,#9bb0c4,#6c6b66 55%,#4a5a3a)"><span class="card-tag">78M WIDE FRONTAGE</span></div>
    <p class="card-text">Nemo enim ipsam voluptatem quia voluptas sit aspernatur aut odit aut fugit, sed quia consequuntur magni dolores eos qui ratione voluptatem.</p>
    <div class="card-foot"><span><svg width="9" height="12" viewBox="0 0 9 12"><path d="M4.5 0A4.5 4.5 0 0 0 0 4.5C0 8 4.5 12 4.5 12S9 8 9 4.5A4.5 4.5 0 0 0 4.5 0z" fill="#777"/></svg>Los Angeles, California</span><span class="card-price">$370,000</span></div>
  </article>
  <article class="card" style="left:451px;top:177px">
    <div class="card-photo" role="img" aria-label="Photo of a large brick family home with a green lawn" style="background:linear-gradient(180deg,#a9c0d6,#7c6a56 55%,#4f6b34)"><span class="card-tag">78M WIDE FRONTAGE</span></div>
    <p class="card-text">Nemo enim ipsam voluptatem quia voluptas sit aspernatur aut odit aut fugit, sed quia consequuntur magni dolores eos qui ratione voluptatem.</p>
    <div class="card-foot"><span><svg width="9" height="12" viewBox="0 0 9 12"><path d="M4.5 0A4.5 4.5 0 0 0 0 4.5C0 8 4.5 12 4.5 12S9 8 9 4.5A4.5 4.5 0 0 0 4.5 0z" fill="#777"/></svg>Los Angeles, California</span><span class="card-price">$370,000</span></div>
  </article>
  <article class="card" style="left:772px;top:177px">
    <div class="card-photo" role="img" aria-label="Photo of a white lake house among autumn trees" style="background:linear-gradient(180deg,#7d8f5a,#c8c8c0 50%,#3f5a6a)"><span class="card-tag">78M WIDE FRONTAGE</span></div>
    <p class="card-text">Nemo enim ipsam voluptatem quia voluptas sit aspernatur aut odit aut fugit, sed quia consequuntur magni dolores eos qui ratione voluptatem.</p>
    <div class="card-foot"><span><svg width="9" height="12" viewBox="0 0 9 12"><path d="M4.5 0A4.5 4.5 0 0 0 0 4.5C0 8 4.5 12 4.5 12S9 8 9 4.5A4.5 4.5 0 0 0 4.5 0z" fill="#777"/></svg>Los Angeles, California</span><span class="card-price">$370,000</span></div>
  </article>

  <article class="card" style="left:130px;top:507px">
    <div class="card-photo" role="img" aria-label="Photo of a stone estate with a fountain in front" style="background:linear-gradient(180deg,#9fb3c6,#8a7a63 50%,#506a3a)"><span class="card-tag">78M WIDE FRONTAGE</span></div>
    <p class="card-text">Nemo enim ipsam voluptatem quia voluptas sit aspernatur aut odit aut fugit, sed quia consequuntur magni dolores eos qui ratione voluptatem.</p>
    <div class="card-foot"><span><svg width="9" height="12" viewBox="0 0 9 12"><path d="M4.5 0A4.5 4.5 0 0 0 0 4.5C0 8 4.5 12 4.5 12S9 8 9 4.5A4.5 4.5 0 0 0 4.5 0z" fill="#777"/></svg>Los Angeles, California</span><span class="card-price">$370,000</span></div>
  </article>
  <article class="card" style="left:451px;top:507px">
    <div class="card-photo" role="img" aria-label="Photo of a wooden deck and lawn behind a home" style="background:linear-gradient(180deg,#3f5a2c,#6b4a32 55%,#4e7a34)"><span class="card-tag">78M WIDE FRONTAGE</span></div>
    <p class="card-text">Nemo enim ipsam voluptatem quia voluptas sit aspernatur aut odit aut fugit, sed quia consequuntur magni dolores eos qui ratione voluptatem.</p>
    <div class="card-foot"><span><svg width="9" height="12" viewBox="0 0 9 12"><path d="M4.5 0A4.5 4.5 0 0 0 0 4.5C0 8 4.5 12 4.5 12S9 8 9 4.5A4.5 4.5 0 0 0 4.5 0z" fill="#777"/></svg>Los Angeles, California</span><span class="card-price">$370,000</span></div>
  </article>
  <article class="card" style="left:772px;top:507px">
    <div class="card-photo" role="img" aria-label="Photo of a brick house with a tall gabled entrance" style="background:linear-gradient(180deg,#b6c8d8,#8c7d6c 50%,#5a6a48)"><span class="card-tag">78M WIDE FRONTAGE</span></div>
    <p class="card-text">Nemo enim ipsam voluptatem quia voluptas sit aspernatur aut odit aut fugit, sed quia consequuntur magni dolores eos qui ratione voluptatem.</p>
    <div class="card-foot"><span><svg width="9" height="12" viewBox="0 0 9 12"><path d="M4.5 0A4.5 4.5 0 0 0 0 4.5C0 8 4.5 12 4.5 12S9 8 9 4.5A4.5 4.5 0 0 0 4.5 0z" fill="#777"/></svg>Los Angeles, California</span><span class="card-price">$370,000</span></div>
  </article>
</section>

<section class="news">
  <h2>LATEST NEWS</h2>
  <article class="news-item" style="left:130px">
    <div class="news-photo" role="img" aria-label="Photo of a family outside their new home" style="background:linear-gradient(180deg,#9ab0c0,#c8b8a0 55%,#6a7a4a)"></div>
    <div class="news-body">
      <h4>Nulla at diam ornare, aliquam urna</h4>
      <p class="news-date">MAY 25, 2018</p>
      <p>Nulla at diam ornare, aliquam urna vel, commodo urna. Nam id risus a est luctus consectetur quis, eget libero. Suspendisse potenti. Pellentesque magna mattis tristique senectus.</p>
      <p class="news-more">Read More +</p>
    </div>
  </article>
  <article class="news-item" style="left:627px">
    <div class="news-photo" role="img" aria-label="Photo of a couple standing in front of a house" style="background:linear-gradient(180deg,#7a8ea0,#b0a090 50%,#5a6a50)"></div>
    <div class="news-body">
      <h4>Nulla at diam ornare, aliquam urna</h4>
      <p class="news-date">MAY 25, 2018</p>
      <p>Nulla at diam ornare, aliquam urna vel, commodo urna. Nam id risus a est luctus consectetur quis, eget libero. Suspendisse potenti. Pellentesque magna mattis tristique senectus.</p>
      <p class="news-more">Read More +</p>
    </div>
  </article>
</section>

<footer class="site-footer">
  <div class="footer-brand"><span class="brand-mark"></span>HEARTHSTONE</div>
  <div class="social"><span></span><span></span><span></span><span></span></div>

  <div class="footer-col" style="left:368px">
    <h5>CONTACT US</h5>
    <div class="contact-line"><svg width="12" height="16" viewBox="0 0 9 12"><path d="M4.5 0A4.5 4.5 0 0 0 0 4.5C0 8 4.5 12 4.5 12S9 8 9 4.5A4.5 4.5 0 0 0 4.5 0z" fill="#999"/></svg><span>Hearthstone Realty Group<br>418 Lakeview Road, Suite 210</span></div>
    <div class="contact-line"><svg width="14" height="14" viewBox="0 0 14 14"><path d="M3 1l3 3-2 2c1 2 2 3 4 4l2-2 3 3-2 2C6 13 1 8 1 3z" fill="#999"/></svg><span>Phone : +555-014-2290</span></div>
    <div class="contact-line"><svg width="14" height="11" viewBox="0 0 14 11"><rect x=".5" y=".5" width="13" height="10" fill="none" stroke="#999"/><path d="M.5 .5L7 6l6.5-5.5" fill="none" stroke="#999"/></svg><span>info@hearthstonerealty.example</span></div>
  </div>

  <div class="footer-col signup" style="left:652px">
    <h5>SIGN UP TO RECEIVE EMAIL</h5>
    <p>Excepteur sint occaecat cupidatat non proident, sunt in culpa qui</p>
    <input type="email" value="Enter Email">
    <button type="button">SUBSCRIBE</button>
  </div>

  <div class="footer-col quick-links" style="left:952px">
    <h5>QUICK LINKS</h5>
    <a href="#">Home</a>
    <a href="#">Qeno Info</a>
    <a href="#">About Qe No Home</a>
    <a href="#">Downloads</a>
    <a href="#">Contact Us</a>
  </div>

  <p class="copyright">Copyright © Hearthstone Realty Group 2018. All rights reserved.</p>
</footer>

<div class="overlay"></div>
<div class="modal" role="dialog" aria-label="My Market Analysis">
  <span class="modal-close"><svg width="8" height="8" viewBox="0 0 8 8"><path d="M1 1l6 6M7 1L1 7" stroke="#333" stroke-width="1.5"/></svg></span>
  <div class="modal-mark"></div>
  <h3>My Market Analysis</h3>
  <form class="modal-form">
    <input type="text" value="Full Name">
    <input type="text" value="Email Address">
    <input type="text" value="Phone Number">
    <input type="text" value="Address">
    <button type="button">GET STARTED</button>
  </form>
</div>

</body>
</html>
```